Vantro cards

I am in the auto motive, transportation business I would like a business card that is Something cool, modern edgy, having to do with car culture. I offer towing service for high and exotic cars. I also provide towing for collisions and car accidents. I offer open and enclosed transport nationwide.

Target Market(s)

Car culture people high end auto collectors

Industry/Entity Type

Towing car carrier

Contact Information for Business Card

My company colors black yellow and silver

Font styles to use
Serif

```html
<!DOCTYPE html>
<html lang="en">
<head>
<meta charset="UTF-8">
<title>Vantro Business Cards</title>
<link rel="stylesheet" href="https://fonts.googleapis.com/css2?family=Poppins:wght@400;500;600;700&display=swap">
<style>
  :root {
    --page-bg: #0d0d0d;
    --card-bg: #2a2a2c;
    --card-edge: #f2d54a;
    --brand-yellow: #f5d547;
    --text-white: #f2f2f2;
    --text-muted: #d6d6d6;
    --rule-grey: #4a4a4d;
    --emboss-light: #5a5a5d;
    --emboss-dark: #39393b;
  }
  * { box-sizing: border-box; margin: 0; padding: 0; }
  html, body {
    width: 1200px; height: 820px; overflow: hidden;
    background: var(--page-bg);
    font-family: "Poppins", sans-serif;
  }
  .sheet {
    position: relative; width: 1200px; height: 820px;
  }
  .card {
    position: absolute; top: 255px;
    width: 540px; height: 310px;
    background: var(--card-bg);
    border: 2px solid var(--card-edge);
    overflow: hidden;
  }
  .card--front { left: 40px; }
  .card--back { left: 620px; }

  /* Front */
  .brand-mark {
    position: absolute; left: 290px; top: 70px;
    display: flex; align-items: center; gap: 12px;
  }
  .brand-mark__square {
    width: 22px; height: 22px; background: var(--brand-yellow);
  }
  .brand-mark__name {
    font-weight: 700; font-size: 40px; letter-spacing: 2px;
    color: var(--text-white); text-transform: uppercase;
  }
  .holder {
    position: absolute; left: 96px; top: 134px;
  }
  .holder__name {
    font-weight: 600; font-size: 17px; color: var(--brand-yellow);
    text-transform: uppercase; letter-spacing: 0.5px; line-height: 1.2;
  }
  .holder__role {
    font-size: 13px; color: var(--text-muted); line-height: 1.3;
  }
  .divider {
    position: absolute; left: 96px; right: 60px; top: 186px;
    height: 1px; background: var(--rule-grey);
  }
  .contact-list {
    position: absolute; left: 96px; top: 200px;
    list-style: none;
  }
  .contact-list li {
    display: flex; align-items: center; gap: 8px;
    font-size: 13px; color: var(--text-white); line-height: 22px;
  }
  .contact-list svg { width: 13px; height: 13px; flex: none; }
  .address {
    position: absolute; right: 60px; top: 202px;
    text-align: right; font-size: 12px; color: var(--text-muted); line-height: 18px;
  }

  /* Back */
  .back-name {
    position: absolute; right: 40px; top: 34px;
    font-weight: 700; font-size: 46px; letter-spacing: 3px;
    color: var(--text-white); text-transform: uppercase;
  }
  .truck-artwork {
    position: absolute; left: 60px; top: 118px;
    width: 430px; height: 170px;
    border-radius: 40px 40px 10px 60px;
    background: linear-gradient(160deg, var(--emboss-light) 0%, var(--emboss-dark) 80%);
  }
</style>
</head>
<body>
<main class="sheet">
  <section class="card card--front" aria-label="Card front">
    <div class="brand-mark">
      <span class="brand-mark__square"></span>
      <span class="brand-mark__name">Vantro</span>
    </div>

    <div class="holder">
      <p class="holder__name">Marcus Hale</p>
      <p class="holder__role">Managing Director</p>
    </div>

    <div class="divider"></div>

    <ul class="contact-list">
      <li>
        <svg viewBox="0 0 16 16" aria-hidden="true"><path fill="var(--brand-yellow)" d="M3.6 1.5l2.3 2.6-1.3 1.8c.9 2 2.5 3.6 4.5 4.5l1.8-1.3 2.6 2.3-1.4 2.4C6.7 13.6 2.4 9.3 1.2 3z"/></svg>
        044-555 019 284
      </li>
      <li>
        <svg viewBox="0 0 16 16" aria-hidden="true"><rect x="1" y="3" width="14" height="10" fill="var(--brand-yellow)"/><path d="M1 3l7 6 7-6" fill="none" stroke="var(--card-bg)" stroke-width="1.4"/></svg>
        info@vantrotow.com
      </li>
      <li>
        <svg viewBox="0 0 16 16" aria-hidden="true"><g fill="none" stroke="var(--brand-yellow)" stroke-width="1.4"><circle cx="8" cy="8" r="6.5"/><ellipse cx="8" cy="8" rx="2.8" ry="6.5"/><path d="M1.5 8h13M2.5 4.8h11M2.5 11.2h11"/></g></svg>
        www.vantrotow.com
      </li>
    </ul>

    <p class="address">418, Carrier Road West<br>60718, Northfield</p>
  </section>

  <section class="card card--back" aria-label="Card back">
    <p class="back-name">Vantro</p>
    <div class="truck-artwork" role="img" aria-label="Embossed tone-on-tone illustration of a flatbed tow truck"></div>
  </section>
</main>
</body>
</html>
```